LoopVane - A ride hailing server VAR

our Brindle.co profile: https://brindle.co/517loopvane

LOOPVANE offers first world solutions to first world problems. These days, our smartphones are our cameras, our wallets and our ride home. LOOPVANE guarantees that even if your phone is lost or dies, you'll never get stranded again. Simply call or text (SMS) our toll-free number to request a ride, and choose from one of the various services you subscribe to. LOOPVANE verifies your identity through a unique pin, making it possible to request rides through your own account from a stranger's phone via text or phone call. You can also login through our website or our App, making it easier than ever to get home phoneless.

LOOPVANE is a heterogeneous ride-hailing service that allows users for request transportation from any "transportation network company," taxi, helicopter service, jet service or any transportation service company that is publicly available. LOOPVANE will allow users to connect through our site, automated phone system, App or any appropriated touch point available.

Target Market(s)

RIde Haling

Coding

Coded - Design and coding required

Number of Pages Required

4 page

Requirements
Must have
• hav
Nice to have
• e the same functionality as our competitor's site: https://hopquill.com/
Should not have
• should not be cheezy
• We need to have the registration/sign up on the main page like https://www.zarvix.com/

```html
<!DOCTYPE html>
<html lang="en">
<head>
<meta charset="utf-8">
<title>LoopVane – Request a ride anytime</title>
<link href="https://fonts.googleapis.com/css2?family=Open+Sans:wght@300;400;600;700&display=swap" rel="stylesheet">
<style>
:root{
  --orange:#f5a800;
  --orange-text:#e08a00;
  --ink:#555555;
  --ink-dark:#444444;
  --band:#f2f2f2;
  --footer:#474747;
  --footer-text:#e6e6e6;
  --btn-dark:#555555;
  --white:#ffffff;
}
*{box-sizing:border-box;margin:0;padding:0}
html,body{width:1200px;height:1024px;overflow:hidden;background:var(--white);font-family:"Open Sans",Arial,sans-serif;color:var(--ink)}
.page{position:relative;width:1200px;height:1024px}

.site-header{position:absolute;top:0;left:0;width:1200px;height:112px}
.brand{position:absolute;left:132px;top:24px;display:flex;align-items:center;gap:12px}
.brand-mark{width:64px;height:64px;border-radius:5px;background:var(--orange)}
.brand-name{font-size:50px;font-weight:400;color:var(--ink);letter-spacing:-.5px;line-height:1}
.main-nav{position:absolute;top:48px;left:584px;display:flex;gap:31px;font-size:13px}
.main-nav a{color:var(--ink);text-decoration:none}
.main-nav a.active{color:var(--orange-text)}
.auth{position:absolute;top:38px;left:863px;display:flex;gap:8px}
.btn{display:flex;align-items:center;justify-content:center;gap:6px;height:40px;width:80px;border-radius:2px;font-size:13px;color:var(--white);text-decoration:none}
.btn-signin{background:var(--btn-dark)}
.btn-signup{background:var(--orange);color:#222}

.hero{position:absolute;top:112px;left:0;width:1200px;height:400px;background:linear-gradient(90deg,#2a1d14 0%,#3b2a1c 40%,#6b4a2c 65%,#3a2718 100%)}
.hero-copy{position:absolute;left:132px;top:133px;color:#e8e8e8}
.hero-kicker{font-size:25px;font-weight:300}
.hero-title{font-size:33px;font-weight:700;letter-spacing:.3px;margin-top:-2px}
.btn-play{display:inline-flex;align-items:center;gap:10px;margin-top:16px;height:45px;padding:0 18px;border:1px solid #e8e8e8;border-radius:3px;color:var(--white);font-size:17px;text-decoration:none}
.slide-arrow{position:absolute;top:185px;width:28px;height:28px;border-radius:50%;background:rgba(0,0,0,.35);display:flex;align-items:center;justify-content:center}
.slide-arrow.prev{left:23px}.slide-arrow.next{left:1148px}

.services{position:absolute;top:512px;left:0;width:1200px;height:102px;background:var(--band);display:flex;align-items:center;font-size:17px;color:var(--ink-dark)}
.services .lead{position:absolute;left:192px}
.services .tail{position:absolute;left:792px}
.partner{position:absolute;font-weight:700;color:var(--ink-dark)}
.partner.zarvix{left:296px;font-size:20px}
.partner.hollin{left:382px;font-size:26px}
.partner.taxi{left:486px;width:82px;height:36px;background:#333;color:var(--white);border-radius:4px;display:flex;align-items:center;justify-content:center;font-size:19px}
.partner.nadrio{left:600px;font-size:34px}

.intro{position:absolute;top:676px;left:130px;width:940px;text-align:center}
.intro p{font-size:17.5px;line-height:24px;color:var(--ink)}
.read-more{display:inline-block;margin-top:17px;font-size:10px;color:var(--orange-text);text-decoration:none}

.features{position:absolute;top:801px;left:132px;display:flex;gap:0}
.feature{width:325px;display:flex;gap:12px}
.feature-icon{width:64px;height:64px;background:var(--orange);border-radius:2px;display:flex;align-items:center;justify-content:center;flex:none}
.feature h2{font-size:25px;font-weight:400;color:var(--ink-dark);line-height:1;margin-top:-1px}
.feature p{font-size:11px;line-height:16px;color:var(--ink);margin-top:12px;width:210px}

.site-footer{position:absolute;top:929px;left:0;width:1200px;height:95px;background:var(--footer);color:var(--footer-text)}
.footer-nav{position:absolute;left:133px;top:26px;font-size:11.5px;display:flex;gap:8px}
.footer-nav a{color:var(--footer-text);text-decoration:none}
.copyright{position:absolute;left:133px;top:53px;font-size:11.5px}
.social{position:absolute;left:1005px;top:36px;display:flex;gap:14px}
.social span{width:24px;height:24px;background:#f2f2f2;border-radius:2px;display:block}
</style>
</head>
<body>
<div class="page">
  <header class="site-header">
    <div class="brand"><span class="brand-mark"></span><span class="brand-name">LoopVane</span></div>
    <nav class="main-nav">
      <a class="active" href="#">Home</a><a href="#">About</a><a href="#">Support</a><a href="#">Contact</a>
    </nav>
    <div class="auth">
      <a class="btn btn-signin" href="#"><svg width="12" height="12" viewBox="0 0 12 12"><path d="M1 5h5V2.5L10 6 6 9.5V7H1z" fill="#fff"/><path d="M8 1h3v10H8" stroke="#fff" fill="none" stroke-width="1.2"/></svg>Sign in</a>
      <a class="btn btn-signup" href="#"><svg width="12" height="12" viewBox="0 0 12 12"><rect x="1" y="2" width="8" height="9" fill="none" stroke="#222" stroke-width="1.2"/><path d="M5 7l5-5 1 1-5 5H5z" fill="#222"/></svg>Sign up</a>
    </div>
  </header>

  <section class="hero" role="img" aria-label="Photo of a woman talking on a mobile phone in a warmly lit interior">
    <div class="hero-copy">
      <div class="hero-kicker">Play this video to know</div>
      <div class="hero-title">HOW LOOPVANE WORKS</div>
      <a class="btn-play" href="#"><svg width="16" height="16" viewBox="0 0 16 16"><circle cx="8" cy="8" r="8" fill="#fff"/><path d="M6 4.5l5 3.5-5 3.5z" fill="#3a2a1c"/></svg>Play This Video</a>
    </div>
    <span class="slide-arrow prev"><svg width="12" height="14" viewBox="0 0 12 14"><path d="M9 1L3 7l6 6" stroke="#ddd" stroke-width="3" fill="none"/></svg></span>
    <span class="slide-arrow next"><svg width="12" height="14" viewBox="0 0 12 14"><path d="M3 1l6 6-6 6" stroke="#ddd" stroke-width="3" fill="none"/></svg></span>
  </section>

  <section class="services">
    <span class="lead">Request an</span>
    <span class="partner zarvix">Zarvix</span>
    <span class="partner hollin">Hollin</span>
    <span class="partner taxi">TAXI</span>
    <span class="partner nadrio">Nadrio</span>
    <span class="tail">anytime without your phone!</span>
  </section>

  <section class="intro">
    <p>LOOPVANE offers first world solutions to first world problems. These days, our smartphones are our cameras, our wallets and our ride home. LOOPVANE guarantees that even if your phone is lost or dies, you'll never get stranded again.</p>
    <a class="read-more" href="#">READ MORE ▸</a>
  </section>

  <section class="features">
    <div class="feature">
      <span class="feature-icon"><svg width="34" height="34" viewBox="0 0 34 34" fill="none" stroke="#333" stroke-width="1.3"><rect x="1" y="1" width="32" height="32"/><path d="M8 26l2-6 13-13 4 4-13 13z"/><path d="M10 20l4 4M20 10l4 4"/></svg></span>
      <div><h2>Signup Now</h2><p>Fusce purus nulla, finibus nec nisl id, ultric ies scelerisque sapien.</p></div>
    </div>
    <div class="feature">
      <span class="feature-icon"><svg width="40" height="40" viewBox="0 0 40 40" fill="none" stroke="#333" stroke-width="1.3"><circle cx="20" cy="14" r="8"/><path d="M4 36c1-8 8-12 11-13M36 36c-1-8-8-12-11-13"/></svg></span>
      <div><h2>Add a new rider</h2><p>Fusce purus nulla, finibus nec nisl id, ultric ies scelerisque sapien.</p></div>
    </div>
    <div class="feature">
      <span class="feature-icon"><svg width="44" height="44" viewBox="0 0 44 44" fill="none" stroke="#333" stroke-width="1.4"><circle cx="22" cy="22" r="20"/><circle cx="22" cy="22" r="8"/><path d="M16 16L9 9M28 16l7-7M16 28l-7 7M28 28l7 7"/></svg></span>
      <div><h2>Support</h2><p>Fusce purus nulla, finibus nec nisl id, ultric ies scelerisque sapien.</p></div>
    </div>
  </section>

  <footer class="site-footer">
    <nav class="footer-nav">
      <a href="#">Home</a><span>|</span><a href="#">About</a><span>|</span><a href="#">Support</a><span>|</span><a href="#">Contact</a><span>|</span><a href="#">Sign in</a><span>|</span><a href="#">Sign up</a>
    </nav>
    <div class="copyright">Copyright © 2017 Company name. All rights reserved.</div>
    <div class="social"><span></span><span></span></div>
  </footer>
</div>
</body>
</html>
```